New Business Card Design Project

Need a design that will create an impact / strong impression towards our clients for our business. We are in the lighting business and we do lighting retrofits for large commercial to industrial clientele.

Target Market(s)

Lighting Industry

Industry/Entity Type

Business

Font styles to use
Other font styles liked:
• we would like to use the font on our logo, not sure what it is though..

Requirements
Must have
• Our logo.
Nice to have
• We are open to suggestions that have to do with lighting.

```html
<!DOCTYPE html>
<html lang="en">
<head>
<meta charset="utf-8">
<title>Tarvinel Retrofit Group – Business Card</title>
<link rel="stylesheet" href="https://fonts.googleapis.com/css2?family=Roboto:wght@400;500&family=Roboto+Condensed:wght@700&display=swap">
<style>
  :root {
    --backdrop: #5b4a3a;
    --paper: #f2f2f2;
    --green-deep: #10370f;
    --green-mid: #0b7a37;
    --green-light: #6cc04a;
    --ink: #4a4a4a;
    --white: #f4f4f4;
  }
  html, body {
    margin: 0;
    width: 1200px;
    height: 960px;
    overflow: hidden;
    background: var(--backdrop);
  }
  .canvas { position: relative; width: 1200px; height: 960px; }
  .card {
    position: absolute;
    width: 600px;
    height: 343px;
    box-sizing: border-box;
    box-shadow: 1px 2px 3px rgba(0,0,0,0.45);
  }
  .card--front { left: 314px; top: 113px; background: var(--paper); }
  .card--back { left: 311px; top: 472px; background: var(--green-deep); }

  .front__tab {
    position: absolute; left: 0; top: 47px;
    width: 15px; height: 41px; background: var(--green-deep);
  }
  .person { position: absolute; left: 33px; top: 46px; }
  .person__name {
    margin: 0;
    font: 700 25px/1 "Roboto Condensed", sans-serif;
    color: var(--green-deep);
  }
  .person__role {
    margin: 4px 0 0;
    font: 700 16px/1 "Roboto Condensed", sans-serif;
    color: var(--green-mid);
  }
  .front__rule {
    position: absolute; left: 33px; top: 97px;
    width: 535px; height: 1px; background: var(--green-mid);
  }
  .brand {
    position: absolute; right: 32px; top: 50px;
    display: flex; align-items: center; gap: 10px;
  }
  .brand__mark { width: 16px; height: 16px; background: var(--green-mid); }
  .brand__name {
    font: 700 32px/1 "Roboto Condensed", sans-serif;
    color: var(--green-deep);
    letter-spacing: 0.5px;
  }
  .brand__sub {
    position: absolute; right: 32px; top: 103px;
    font: 700 10.5px/1 "Roboto Condensed", sans-serif;
    color: var(--green-deep);
    letter-spacing: 1.3px;
  }

  .contact {
    position: absolute; left: 33px; top: 236px;
    margin: 0; padding: 0; list-style: none;
  }
  .contact__item {
    display: flex; align-items: center; gap: 9px;
    height: 19px;
    font: 400 14.5px/1 "Roboto", sans-serif;
    color: var(--ink);
  }
  .contact__icon { width: 13px; height: 13px; fill: var(--green-deep); }
  .address {
    position: absolute; right: 32px; top: 258px;
    font: 400 14.5px/19px "Roboto", sans-serif;
    color: var(--ink);
    text-align: right;
    font-style: normal;
  }
  .address__web { letter-spacing: 0.6px; }

  .back__brand {
    position: absolute; left: 0; right: 0; top: 142px;
    display: flex; justify-content: center; align-items: center; gap: 14px;
  }
  .back__mark { width: 30px; height: 30px; background: var(--green-light); }
  .back__name {
    font: 700 44px/1 "Roboto Condensed", sans-serif;
    color: var(--white);
    letter-spacing: 1px;
  }
  .back__web {
    position: absolute; left: 0; right: 0; top: 283px;
    text-align: center;
    font: 400 14.5px/1 "Roboto", sans-serif;
    color: var(--white);
    letter-spacing: 3.2px;
  }
</style>
</head>
<body>
<main class="canvas">
  <section class="card card--front" aria-label="Business card front">
    <div class="front__tab"></div>
    <div class="person">
      <h1 class="person__name">DANIEL REEVE</h1>
      <p class="person__role">CEO/FOUNDER</p>
    </div>
    <div class="brand">
      <span class="brand__mark"></span>
      <span class="brand__name">TARVINEL</span>
    </div>
    <div class="front__rule"></div>
    <div class="brand__sub">TARVINEL RETROFIT GROUP, LLC.</div>

    <ul class="contact">
      <li class="contact__item">
        <svg class="contact__icon" viewBox="0 0 16 16" aria-hidden="true"><path d="M3.6 1.2 6 3.6 4.6 5.6c.9 2.2 3.5 4.8 5.8 5.8l2-1.4 2.4 2.4-1.6 2.2C8 14.4 1.6 8 1.4 2.8z"/></svg>
        555 201 3846
      </li>
      <li class="contact__item">
        <svg class="contact__icon" viewBox="0 0 16 16" aria-hidden="true"><path d="M4 0h8a1 1 0 0 1 1 1v14a1 1 0 0 1-1 1H4a1 1 0 0 1-1-1V1a1 1 0 0 1 1-1zm1 2v10h6V2zm3 11a1 1 0 1 0 0 2 1 1 0 0 0 0-2z"/></svg>
        555 307 4412
      </li>
      <li class="contact__item">
        <svg class="contact__icon" viewBox="0 0 16 16" aria-hidden="true"><path d="M4 1h8v4H4zM1 6h14v6h-2v-2H3v2H1zm3 5h8v4H4z"/></svg>
        555 419 2075
      </li>
      <li class="contact__item">
        <svg class="contact__icon" viewBox="0 0 16 16" aria-hidden="true"><path d="M1 3h14v1.2L8 9 1 4.2zm0 2.6 7 4.8 7-4.8V13H1z"/></svg>
        daniel@tarvinel-lighting.com
      </li>
    </ul>

    <address class="address">
      214 Alder Court<br>
      Fairview, Oregon 97024<br>
      <span class="address__web">www.tarvinel-lighting.com</span>
    </address>
  </section>

  <section class="card card--back" aria-label="Business card back">
    <div class="back__brand">
      <span class="back__mark"></span>
      <span class="back__name">TARVINEL</span>
    </div>
    <div class="back__web">www.tarvinelretrofitgroup.com</div>
  </section>
</main>
</body>
</html>
```